Cleaning service website design

We need a new nice web design(logo will be the same) for a new cleaning service Company:

Informations about Company and logo you can take from flyers in attachments.

This is a cleaning service Company which have simple rules and we would like to show that(in checklist form) on website:

- What we do and that we're Cleaning Green

- Why us?

- How much(our pricing is simple)

Also we would like to communicate with clients by some nice/big pictures on website and the most important thing is our phone number and short/fast Brimtallow.

Also there should be some space for description about our Company.

Generally all information on main page can be short: about us, about service(what we do), last reviews, tips (for example: Tip of the week) and other can be some introduction to subpage where will be more information.

There will be few subpages like: About us, About our service, Photos(Before and after), Reviews , Tips, FAQ, Contact, Looking for a Job? - most of them will be just text so you can project just one example.

```html
<!DOCTYPE html>
<html lang="en">
<head>
<meta charset="utf-8">
<title>Tidy Nest – Cleaning Service</title>
<link href="https://fonts.googleapis.com/css2?family=PT+Sans:wght@400;700&family=PT+Sans+Narrow:wght@400;700&display=swap" rel="stylesheet">
<style>
:root{
  --green:#6cbf4a;
  --green-dark:#4f9a2d;
  --orange:#f7941d;
  --ink:#222;
  --muted:#8a8a8a;
  --footer:#262626;
  --footer-base:#1b1b1b;
  --line:#d8d8d8;
}
*{margin:0;padding:0;box-sizing:border-box}
html,body{width:1082px;height:1200px;overflow:hidden;background:#fff;font-family:"PT Sans",sans-serif;color:var(--ink)}
.page{position:relative;width:1082px;height:1200px}
.header{position:absolute;top:0;left:0;width:1082px;height:121px;border-bottom:5px solid #eee}
.brand{position:absolute;left:135px;top:22px;display:flex;align-items:center;gap:10px}
.brand-dot{width:34px;height:34px;border-radius:50%;background:var(--green)}
.brand-name{font-size:30px;font-weight:700;color:var(--green-dark)}
.call{position:absolute;right:135px;top:12px;text-align:right}
.call-label{font-size:13px;color:#333}
.call-label b{font-weight:700}
.call-number{display:flex;align-items:center;justify-content:flex-end;gap:6px;font-size:24px;font-weight:700;margin-top:1px}
.nav{position:absolute;right:135px;top:60px;display:flex;font-family:"PT Sans Narrow",sans-serif;font-weight:700;font-size:12.5px}
.nav a{display:block;height:61px;line-height:52px;padding:0 15px;color:#333;text-decoration:none}
.nav a.active{background:#f0f0f0;color:var(--green);border-bottom:4px solid var(--green)}
.nav a:last-child{padding-right:0}
.hero{position:absolute;top:121px;left:0;width:1082px;height:453px;background:radial-gradient(ellipse at 40% 55%,#c6cf6a 0%,#8aa53a 35%,#4f6e1f 70%,#2f4413 100%)}
.hero-photo{position:absolute;inset:0}
.hero-copy{position:absolute;left:135px;top:40px;color:#fff;text-shadow:0 1px 3px rgba(0,0,0,.45)}
.hero-kicker{font-size:30px;font-weight:400;line-height:1.1}
.hero-title{font-size:29px;font-weight:700;line-height:1.3}
.hero-sub{font-size:19px;font-weight:700;margin-top:4px}
.hero-sub span{color:var(--orange)}
.checklist{list-style:none;margin-top:38px}
.checklist li{display:flex;align-items:center;gap:12px;font-size:13px;height:30.5px}
.btn-start{position:absolute;left:135px;top:339px;width:222px;height:52px;border-radius:5px;background:linear-gradient(#ffb21c,#f57c00);color:#fff;font-weight:700;font-size:24px;display:flex;align-items:center;justify-content:center;gap:10px;text-shadow:0 1px 2px rgba(0,0,0,.25)}
.seal{position:absolute;left:386px;top:306px}
.features{position:absolute;top:602px;left:135px;width:811px;display:flex;justify-content:space-between}
.card{position:relative;width:256px;height:167px;background:linear-gradient(#f7f7f7,#ececec);border:1px solid #e6e6e6;padding:20px 21px}
.card h3{text-align:center;color:var(--green);font-size:17px;font-weight:400;margin-bottom:8px}
.card p{font-size:11px;line-height:21px;color:var(--muted);white-space:nowrap}
.more{position:absolute;left:21px;top:124px;width:54px;height:17px;border-radius:2px;background:linear-gradient(#6fc94a,#3f9a1c);color:#fff;font-size:10.5px;text-align:center;line-height:17px;font-weight:700}
.card-icon{position:absolute;right:20px;top:88px}
.about{position:absolute;top:800px;left:135px;width:811px;text-align:center}
.about-head{display:flex;align-items:center;gap:16px}
.about-head span{flex:1;height:4px;border-top:1px solid var(--line);border-bottom:1px solid var(--line)}
.about-head h2{font-family:"PT Sans Narrow",sans-serif;font-weight:400;font-size:27px}
.about p{font-size:12px;line-height:17px;color:#777;margin-top:32px}
.about a{color:var(--green);text-decoration:none}
.footer{position:absolute;top:953px;left:0;width:1082px;height:213px;background:var(--footer);color:#fff}
.fcol{position:absolute;top:34px}
.fcol h4{font-size:15px;font-weight:700;margin-bottom:12px}
.fcol ul{list-style:none}
.fcol li{font-size:11px;height:21px;padding-left:2px}
.newsletter p{font-size:11px;margin-bottom:9px}
.signup{display:flex;gap:6px}
.signup .field{width:275px;height:36px;background:#fff;border-radius:3px;color:#333;font-size:11px;line-height:36px;padding-left:14px}
.signup .go{width:38px;height:36px;border-radius:3px;background:linear-gradient(#ffb21c,#f57c00);font-weight:700;font-size:13px;text-align:center;line-height:36px}
.socials{display:flex;gap:9px;margin-top:30px}
.socials span{width:21px;height:21px;border-radius:2px}
.foot-brand{position:absolute;right:135px;top:150px;display:flex;align-items:center;gap:6px;font-size:17px;font-weight:700;color:var(--green)}
.foot-brand i{width:16px;height:16px;border-radius:50%;background:var(--green)}
.basebar{position:absolute;top:1166px;left:0;width:1082px;height:34px;background:var(--footer-base);color:#555;font-size:11px;line-height:34px;padding-left:135px}
</style>
</head>
<body>
<div class="page">
  <header class="header">
    <div class="brand"><span class="brand-dot"></span><span class="brand-name">Tidy Nest</span></div>
    <div class="call">
      <div class="call-label"><b>Call Us</b> to arrange your cleaning on</div>
      <div class="call-number">
        <svg width="16" height="20" viewBox="0 0 16 20"><path d="M4 1 L7 5 L5 7 Q6 11 9 14 L11 12 L15 15 L13 18 Q8 19 4 13 Q0 7 4 1Z" fill="#1f6fb5"/></svg>
        555-014-2290
      </div>
    </div>
    <nav class="nav">
      <a class="active">HOME</a><a>ABOUT US</a><a>OUR SERVICES</a><a>PHOTOS</a><a>REVIEWS</a><a>TIPS</a><a>CAREERS</a><a>FAQ</a><a>CONTACT</a>
    </nav>
  </header>

  <section class="hero">
    <div class="hero-photo" role="img" aria-label="Photo of a woman stretching her arms joyfully on a sunlit forest path"></div>
    <div class="hero-copy">
      <div class="hero-kicker">Affordably</div>
      <div class="hero-title">making your life Simpler!</div>
      <div class="hero-sub">Imagine! House cleaning as&nbsp; low as <span>$79</span></div>
      <ul class="checklist">
        <li><svg width="22" height="22" viewBox="0 0 22 22"><path d="M2 20 Q3 6 20 2 Q18 18 2 20Z" fill="#7ccf3c"/></svg>We use quality products so your house looks and smells the way you love</li>
        <li><svg width="22" height="22" viewBox="0 0 22 22"><path d="M2 20 Q3 6 20 2 Q18 18 2 20Z" fill="#7ccf3c"/></svg>Our all staff are police checked, honest trained cleaning professionals</li>
        <li><svg width="22" height="22" viewBox="0 0 22 22"><path d="M2 20 Q3 6 20 2 Q18 18 2 20Z" fill="#7ccf3c"/></svg>We provide reguler, weekly, fortnightly or monthly cleaning</li>
        <li><svg width="22" height="22" viewBox="0 0 22 22"><path d="M2 20 Q3 6 20 2 Q18 18 2 20Z" fill="#7ccf3c"/></svg>We are 100% Eco friendly!</li>
      </ul>
    </div>
    <div class="btn-start">GET STARTED
      <svg width="26" height="22" viewBox="0 0 26 22"><path d="M0 7 H13 V0 L26 11 L13 22 V15 H0Z" fill="#fff"/></svg>
    </div>
    <svg class="seal" width="104" height="104" viewBox="0 0 104 104">
      <circle cx="52" cy="52" r="51" fill="#6cb83a"/>
      <circle cx="52" cy="52" r="44" fill="#7fc84a"/>
      <text x="52" y="58" text-anchor="middle" font-family="PT Sans,sans-serif" font-weight="700" font-size="24" fill="#fff">100%</text>
      <rect x="6" y="66" width="92" height="22" rx="3" fill="#e2e2e2"/>
      <text x="52" y="82" text-anchor="middle" font-family="PT Sans,sans-serif" font-weight="700" font-size="13" fill="#999">GUARANTEE</text>
      <text x="52" y="28" text-anchor="middle" font-family="PT Sans,sans-serif" font-size="10" fill="#e9f6df">SATISFACTION</text>
    </svg>
  </section>

  <section class="features">
    <article class="card">
      <h3>Why Us</h3>
      <p>Lorem ipsum dolor sit amet consectetur<br>adipiscing elit duis ante ut magna<br>is a dummy text.</p>
      <div class="more">more</div>
      <div class="card-icon" role="img" aria-label="Cleaning supplies illustration" style="width:58px;height:58px;background:linear-gradient(135deg,#f4b82a,#5a4fc0 55%,#1f8fe0);border-radius:8px"></div>
    </article>
    <article class="card">
      <h3>Pricing</h3>
      <p>Sed ut parspatisas ante dolore ut magna<br>nisi, Aliquam vestibulum nabi<br>jane, mowla jane.</p>
      <div class="more">more</div>
      <div class="card-icon" role="img" aria-label="Stack of banknotes illustration" style="width:74px;height:60px;background:linear-gradient(135deg,#9ee06a,#4aa423);border-radius:8px"></div>
    </article>
    <article class="card">
      <h3>That We Are Eco</h3>
      <p>Aliquam magna nisi tortor ut aliquam elit<br>ante dolore is a standard simply<br>dummy text.</p>
      <div class="more">more</div>
      <svg class="card-icon" width="62" height="62" viewBox="0 0 62 62"><circle cx="31" cy="31" r="30" fill="#5fae34"/><circle cx="31" cy="31" r="26" fill="#72c043"/><path d="M31 50 V28 M31 30 Q20 30 17 20 Q28 19 31 28 M31 30 Q42 30 45 20 Q34 19 31 28" stroke="#fff" stroke-width="3" fill="#fff"/></svg>
    </article>
  </section>

  <section class="about">
    <div class="about-head"><span></span><h2>About Tidy Nest.com</h2><span></span></div>
    <p>Lorem ipsum dolor sit amet consectetur adipiscing elit duis, ante dolore ut aliquam magna tortor nisi is a simply standard dummy text for the<br>typesetting industry worldwide. You can add your own text by replaceing this dummy text.<br>Parspatisas ante dolore ut aliquam magna nisi is also a dummy text. <a>Find out more.</a></p>
  </section>

  <footer class="footer">
    <div class="fcol" style="left:135px"><h4>Quick Links</h4><ul><li>Home</li><li>About Us</li><li>About Our Service</li><li>Photos</li><li>Contact</li></ul></div>
    <div class="fcol" style="left:298px"><h4>Useful Links</h4><ul><li>Terms of use</li><li>Privacy Policy</li><li>Help Center</li><li>Community</li><li>Login Area</li></ul></div>
    <div class="fcol" style="left:443px"><h4>Join Our Community</h4><ul><li>Social Page</li><li>Microblog</li><li>Pro Network</li></ul></div>
    <div class="fcol newsletter" style="left:627px">
      <h4>SignUp For Our Monthly Newsletter</h4>
      <p>Subscribe our newsletter &amp; get the latest news &amp; updates</p>
      <div class="signup"><div class="field">Email Address</div><div class="go">GO</div></div>
      <div class="socials"><span style="background:#2d5fb0"></span><span style="background:#37a7e0"></span><span style="background:#f3a21b"></span></div>
    </div>
    <div class="foot-brand"><i></i>Tidy Nest</div>
  </footer>
  <div class="basebar">© 2013 by, Tidy Nest. All Rights Reserved.</div>
</div>
</body>
</html>
```